Marcus Delbridge Finance

Need a personal website advertising Equipment Finance,Business Finance,Commercial Finance, Construction Finance, Bridging Finance. Similar websites are www.corvalend.com.au / www.tarmivest.com.au / www.qbr7.com.au /wwwhalvecredit.com.au

Target Market(s)

Business People

Industry/Entity Type

Business

Number of Pages Required

3 page

Font styles to use
Serif
Sans Serif

Requirements
Must have
• All i want is a simple corporate looking website advertising Equipment Finance, Commercial Finance, Construction Finance, Business Finance, Bridging Finance,

```html
<!DOCTYPE html>
<html lang="en">
<head>
<meta charset="utf-8">
<title>Marcus Delbridge Finance</title>
<link href="https://fonts.googleapis.com/css2?family=Roboto:wght@400;500;700&family=Roboto+Condensed:wght@400;700&display=swap" rel="stylesheet">
<style>
:root{
  --brand:#1f4fa0;
  --brand-dark:#1e3a82;
  --footer:#2b4c9e;
  --sky-a:#3576c0;
  --sky-b:#4d98da;
  --ink:#222;
  --muted:#666;
  --line:#d6d6d6;
  --dark:#2a2d33;
  --white:#fff;
}
*{box-sizing:border-box;margin:0;padding:0}
html,body{width:1200px;height:3243px;overflow:hidden}
body{font-family:"Roboto",sans-serif;color:var(--ink);background:var(--white);font-size:13px}
.container{width:1006px;margin:0 auto;position:relative;height:100%}
.section{position:relative;width:1200px}
.heading{font-family:"Roboto Condensed",sans-serif;font-weight:400;font-size:30px;text-align:center;letter-spacing:.5px;color:var(--ink)}

/* header */
.site-header{height:113px;border-bottom:1px solid #eee}
.brand{position:absolute;left:0;top:24px;color:var(--brand);font-weight:700;line-height:1}
.brand-top{font-size:42px;letter-spacing:1px}
.brand-sub{font-size:16px;margin-top:2px}
.contact-bar{position:absolute;right:0;top:18px;display:flex;gap:26px;font-size:14px;color:#444;align-items:center}
.contact-bar span{display:flex;align-items:center;gap:10px}
.ic-circle{width:28px;height:28px;border:1px solid #555;border-radius:50%;display:flex;align-items:center;justify-content:center}
.main-nav{position:absolute;right:0;top:72px;display:flex;gap:40px;font-size:13px;color:#333}
.main-nav a{color:inherit;text-decoration:none;padding-bottom:12px}
.main-nav a.active{color:var(--brand);border-bottom:2px solid var(--brand)}

/* hero */
.hero{height:529px}
.hero-photo{position:absolute;inset:0;background:linear-gradient(100deg,#f1f3f6 0%,#e5e9ef 35%,#8d98ab 55%,#3d4454 75%,#b9bfca 100%)}
.hero-copy{position:absolute;left:97px;top:118px}
.hero-copy h1{font-family:"Roboto Condensed",sans-serif;font-weight:700;color:var(--brand);font-size:38px;line-height:1.2}
.hero-copy p{font-size:14px;color:#333;line-height:1.55;margin-top:12px}
.dots{display:flex;gap:5px;margin-top:14px}
.dots i{width:14px;height:14px;border-radius:50%;border:1.5px solid var(--brand)}
.dots i.on{background:var(--brand)}

/* services */
.services{height:478px}
.services .heading{position:absolute;top:68px;width:100%}
.svc{position:absolute;top:160px;width:240px;margin-left:-120px;text-align:center}
.svc-icon{width:94px;height:94px;border-radius:50%;border:1.5px solid var(--brand);margin:0 auto;display:flex;align-items:center;justify-content:center}
.svc h3{font-weight:400;font-size:17px;margin-top:26px}
.svc p{font-size:11.5px;color:var(--muted);line-height:1.55;margin-top:10px}
.svc a{display:inline-block;font-size:12px;color:#222;margin-top:22px;text-decoration:none}
.slider-arrow{position:absolute;top:245px;width:30px;height:30px;border-radius:50%;border:1px solid var(--line);display:flex;align-items:center;justify-content:center}

/* welcome */
.welcome{height:388px;background:linear-gradient(110deg,var(--sky-a),var(--sky-b) 60%,#3f86cb);color:var(--white);text-align:center}
.welcome h2{font-family:"Roboto Condensed",sans-serif;font-weight:700;font-size:33px;padding-top:88px}
.welcome p{width:940px;margin:22px auto 0;font-size:11px;line-height:1.95}
.btn-outline{display:inline-block;border:1px solid var(--white);color:var(--white);padding:9px 20px;font-size:12.5px;margin-top:22px}

/* planning */
.planning{height:534px}
.monitor{position:absolute;left:134px;top:73px;width:391px;height:374px;background:linear-gradient(160deg,#d0d4da,#7c8594 45%,#c8ccd2);border-radius:6px}
.plan-copy{position:absolute;left:590px;top:90px;width:520px}
.plan-copy h2{font-family:"Roboto Condensed",sans-serif;font-weight:400;font-size:29px}
.plan-copy>p{font-size:11.5px;color:var(--muted);line-height:1.6;margin-top:12px}
.feature{display:flex;gap:18px;margin-top:22px;align-items:flex-start}
.feature .ring{flex:none;width:62px;height:62px;border-radius:50%;border:1px solid #999;display:flex;align-items:center;justify-content:center}
.feature h4{font-weight:400;font-size:15px;margin-top:-4px}
.feature p{font-size:11.5px;color:var(--muted);line-height:1.6;margin-top:6px}

/* testimonials */
.testimonials{height:340px;background:linear-gradient(135deg,#33363c,var(--dark) 50%,#24262b);color:var(--white);text-align:center}
.testimonials .heading{color:var(--white);padding-top:66px}
.testimonials blockquote{width:930px;margin:22px auto 0;font-size:12.5px;line-height:1.7;position:relative}
.testimonials blockquote::before{content:"\201C";position:absolute;left:-4px;top:-10px;font-size:26px;font-style:italic}
.cite{margin-top:16px;font-style:italic;font-size:17px}
.cite small{font-size:12px}
.bars{display:flex;gap:6px;justify-content:center;margin-top:18px}
.bars i{width:28px;height:3px;background:#666}
.bars i.on{background:#ddd}

/* blog */
.blog{height:526px}
.blog .heading{padding-top:62px}
.post{position:absolute;top:130px;width:310px}
.post-img{height:179px;position:relative}
.date{position:absolute;left:0;bottom:50px;background:#333;color:var(--white);font-size:13px;line-height:1.25;padding:6px 10px}
.post h3{font-weight:400;font-size:17px;margin-top:18px}
.post p{font-size:11.5px;color:var(--muted);line-height:1.6;margin-top:10px}
.btn-small{display:inline-block;border:1px solid #aaa;color:#333;font-size:11px;padding:6px 10px;margin-top:14px}

/* footer */
.site-footer{height:277px;background:linear-gradient(180deg,var(--footer),#2a49a0);color:var(--white)}
.col{position:absolute;top:52px}
.col h5{font-weight:500;font-size:16px;letter-spacing:.5px}
.col p,.col li{font-size:11.5px;line-height:1.6}
.col ul{list-style:none;margin-top:16px}
.col li{line-height:1.9}
.email-field{width:244px;height:42px;background:var(--white);color:#888;font-size:11px;padding:13px 12px;margin-top:14px}
.btn-dark{display:inline-block;background:#2b2b2b;color:var(--white);font-size:11px;padding:13px 12px;margin-top:14px}
.addr{display:flex;gap:12px;margin-top:14px;font-size:11.5px;line-height:1.5}
.footer-name{position:absolute;left:871px;top:92px;font-size:27px;font-weight:700}
.socials{position:absolute;left:965px;top:136px;display:flex;gap:8px}
.socials i{width:28px;height:28px;border-radius:50%;border:1.5px solid var(--white)}
.copyright{height:58px;background:var(--brand-dark);color:var(--white);font-size:11.5px;text-align:center;line-height:58px}
</style>
</head>
<body>

<header class="section site-header">
  <div class="container">
    <div class="brand"><div class="brand-top">MARCUS</div><div class="brand-sub">Delbridge Finance</div></div>
    <div class="contact-bar">
      <span><span class="ic-circle"><svg width="14" height="14" viewBox="0 0 24 24"><path d="M6.6 10.8a15 15 0 006.6 6.6l2.2-2.2a1 1 0 011-.25 11 11 0 003.6.6 1 1 0 011 1V20a1 1 0 01-1 1A17 17 0 013 4a1 1 0 011-1h3.5a1 1 0 011 1 11 11 0 00.6 3.6 1 1 0 01-.25 1z" fill="#444"/></svg></span>61 7 5550 2840</span>
      <span><span class="ic-circle"><svg width="14" height="12" viewBox="0 0 24 18"><rect x="1" y="1" width="22" height="16" fill="none" stroke="#444" stroke-width="2"/><path d="M1 1l11 9 11-9" fill="none" stroke="#444" stroke-width="2"/></svg></span>info@marcusdelbridge.com</span>
    </div>
    <nav class="main-nav">
      <a class="active">HOME</a><a>ABOUT US</a><a>OUR SERVICES</a><a>BLOG</a><a>CONTACT US</a>
    </nav>
  </div>
</header>

<section class="section hero">
  <div class="hero-photo" role="img" aria-label="Two business people smiling and reviewing a tablet at an office desk with a laptop"></div>
  <div class="hero-copy">
    <h1>MARCUS DELBRIDGE<br>FINANCE</h1>
    <p>Lorem ipsum dolor sit amet, consectetur adipiscing<br>Sed ut perspiciatis unde sed do eiusmod</p>
    <div class="dots"><i class="on"></i><i></i><i></i></div>
  </div>
</section>

<section class="section services">
  <h2 class="heading">OUR SERVICES</h2>
  <div class="slider-arrow" style="left:40px"><svg width="8" height="12" viewBox="0 0 8 12"><path d="M6 1L1 6l5 5" fill="none" stroke="#bbb" stroke-width="1.5"/></svg></div>
  <div class="slider-arrow" style="left:1137px"><svg width="8" height="12" viewBox="0 0 8 12"><path d="M2 1l5 5-5 5" fill="none" stroke="#bbb" stroke-width="1.5"/></svg></div>

  <div class="svc" style="left:204px">
    <div class="svc-icon"><svg width="48" height="44" viewBox="0 0 48 44"><rect x="6" y="22" width="26" height="10" fill="#1f4fa0"/><rect x="16" y="14" width="10" height="8" fill="#1f4fa0"/><path d="M26 16l12-10 6 10" fill="none" stroke="#1f4fa0" stroke-width="3"/><rect x="4" y="34" width="30" height="6" rx="3" fill="none" stroke="#1f4fa0" stroke-width="2.5"/></svg></div>
    <h3>Equipment Finance</h3>
    <p>Lorem ipsum dolor sit amet, consectetur<br>adiscing elit, sed do eiusmod tempor<br>incididunt ut labore et dolore</p>
    <a>CLICK HERE ➜</a>
  </div>
  <div class="svc" style="left:462px">
    <div class="svc-icon"><svg width="48" height="44" viewBox="0 0 48 44"><circle cx="24" cy="13" r="10" fill="#1f4fa0"/><text x="24" y="18" font-size="13" fill="#fff" text-anchor="middle" font-family="Roboto,sans-serif" font-weight="700">$</text><path d="M4 32h12l8 4h10l10-6v4l-10 8H4z" fill="#1f4fa0"/></svg></div>
    <h3>Business Finance</h3>
    <p>Lorem ipsum dolor sit amet, consectetur<br>adiscing elit, sed do eiusmod tempor<br>incididunt ut labore et dolore</p>
    <a>CLICK HERE ➜</a>
  </div>
  <div class="svc" style="left:736px">
    <div class="svc-icon"><svg width="44" height="44" viewBox="0 0 44 44"><circle cx="22" cy="9" r="7" fill="#1f4fa0"/><text x="22" y="13" font-size="10" fill="#fff" text-anchor="middle" font-family="Roboto,sans-serif" font-weight="700">$</text><rect x="8" y="22" width="6" height="16" fill="#1f4fa0"/><rect x="17" y="18" width="6" height="20" fill="#1f4fa0"/><rect x="26" y="22" width="6" height="16" fill="#1f4fa0"/><rect x="35" y="26" width="3" height="12" fill="#1f4fa0"/><rect x="5" y="39" width="34" height="2" fill="#1f4fa0"/></svg></div>
    <h3>Commercial Finance</h3>
    <p>Lorem ipsum dolor sit amet, consectetur<br>adiscing elit, sed do eiusmod tempor<br>incididunt ut labore et dolore</p>
    <a>CLICK HERE ➜</a>
  </div>
  <div class="svc" style="left:994px">
    <div class="svc-icon"><svg width="44" height="48" viewBox="0 0 44 48"><rect x="6" y="14" width="12" height="30" fill="none" stroke="#1f4fa0" stroke-width="2.5"/><rect x="18" y="4" width="12" height="40" fill="none" stroke="#1f4fa0" stroke-width="2.5"/><rect x="30" y="20" width="9" height="24" fill="none" stroke="#1f4fa0" stroke-width="2.5"/><path d="M22 10h4M22 16h4M22 22h4M22 28h4M10 20h4M10 26h4M10 32h4" stroke="#1f4fa0" stroke-width="2"/></svg></div>
    <h3>Construction Finance</h3>
    <p>Lorem ipsum dolor sit amet, consectetur<br>adiscing elit, sed do eiusmod tempor<br>incididunt ut labore et dolore</p>
    <a>CLICK HERE ➜</a>
  </div>
</section>

<section class="section welcome">
  <h2>WELCOME TO MARCUS DELBRIDGE FINANCE</h2>
  <p>Mr. Marcus Delbridge serves as Operations Director of Halden Financial Services Pty Ltd. Mr. Delbridge has 16 years experience in the Financial Services and bridging Finance industry, both in Australia, as well as in South Africa. He was employed by the South African based business (BROADWAY FINANCE) for the majority of its operation. He held senior operational positions within Broadway Finance and provided staff support and direction, training and operational control for the Company. Since the establishment of Halden Financial Services, Mr. Delbridge has implemented constant Procedures, Policy and system updates to products in order to meet market demands and to minimize risk on Bridging loans originated</p>
  <span class="btn-outline">READ MORE</span>
</section>

<section class="section planning">
  <div class="monitor" role="img" aria-label="Desktop computer monitor showing a person working on a laptop at a desk"></div>
  <div class="plan-copy">
    <h2>FINANCIAL PLANNING</h2>
    <p>Lorem ipsum dolor sit amet, consectetur adipiscing elit, sed do eiusmod tempor incididunt ut labore et dolore magna aliqua. Ut enim ad minim veniam, quis nostrud exercitation</p>
    <div class="feature">
      <div class="ring"><svg width="26" height="20" viewBox="0 0 26 20"><rect x="1" y="1" width="24" height="18" rx="2" fill="none" stroke="#333" stroke-width="1.8"/><rect x="1" y="6" width="24" height="3" fill="#333"/><rect x="4" y="13" width="8" height="2" fill="#333"/></svg></div>
      <div><h4>TRANSPARENCY AND AUTHENTICITY</h4><p>Lorem ipsum dolor sit amet, consectetur adipiscing elit, sed do<br>eiusmod tempor incididunt ut labore et dolore magna</p></div>
    </div>
    <div class="feature">
      <div class="ring"><svg width="24" height="22" viewBox="0 0 24 22"><path d="M1 1v20h22" fill="none" stroke="#333" stroke-width="1.8"/><path d="M4 16l5-6 4 4 8-9" fill="none" stroke="#333" stroke-width="1.8"/></svg></div>
      <div><h4>DATA DRIVEN INVESTMENT</h4><p>Lorem ipsum dolor sit amet, consectetur adipiscing elit, sed do<br>eiusmod tempor incididunt ut labore et dolore magna</p></div>
    </div>
    <div class="feature">
      <div class="ring"><svg width="28" height="20" viewBox="0 0 28 20"><rect x="4" y="1" width="20" height="14" fill="none" stroke="#333" stroke-width="1.8"/><path d="M1 18h26" stroke="#333" stroke-width="2"/></svg></div>
      <div><h4>MODERN TECHNOLOGY</h4><p>Lorem ipsum dolor sit amet, consectetur adipiscing elit, sed do<br>eiusmod tempor incididunt ut labore et dolore magna</p></div>
    </div>
  </div>
</section>

<section class="section testimonials">
  <h2 class="heading">TESTIMONIALS</h2>
  <blockquote>Lorem ipsum dolor sit amet, consectetur adipiscing elit, sed do eiusmod tempor incididunt ut labore et dolore magna aliqua. Ut enim ad minim veniam, quis nostrud exercitation ullamco laboris nisi ut aliquip ex ea commodo consequat. Duis aute irure dolor in reprehenderit in voluptate velit esse cillum dolore eu fugiat nulla Sed ut perspiciatis unde omnis iste natus error sit voluptatem accusantium doloremque laudantium, totam rem aperiam, eaque ipsa quae ab illo inventore veritatis et quasi architecto beatae vitae</blockquote>
  <div class="cite">Jane Roe - <small>Marcus Delbridge</small></div>
  <div class="bars"><i class="on"></i><i></i><i></i></div>
</section>

<section class="section blog">
  <h2 class="heading">LATEST BLOG</h2>
  <article class="post" style="left:97px">
    <div class="post-img" role="img" aria-label="Hands using a calculator beside financial papers" style="background:linear-gradient(135deg,#dfe6ee,#9fb4c9 60%,#e8edf2)"><div class="date">SEP<br>09<br>2017</div></div>
    <h3>Nemo enim ipsam voluptatem quia</h3>
    <p>Sed ut perspiciatis unde omnis iste natus error sit uptatem accusantium doloremque laudantium, totam rem aperiam, eaque ipsa quae ab illo inventore veritatis</p>
    <span class="btn-small">READ MORE</span>
  </article>
  <article class="post" style="left:445px">
    <div class="post-img" role="img" aria-label="Laptop on a desk with printed charts and a pen" style="background:linear-gradient(135deg,#c9a99c,#e6e3e0 50%,#b7c3d0)"><div class="date">SEP<br>09<br>2017</div></div>
    <h3>Nemo enim ipsam voluptatem quia</h3>
    <p>Sed ut perspiciatis unde omnis iste natus error sit uptatem accusantium doloremque laudantium, totam rem aperiam, eaque ipsa quae ab illo inventore veritatis</p>
    <span class="btn-small">READ MORE</span>
  </article>
  <article class="post" style="left:791px">
    <div class="post-img" role="img" aria-label="Businessman in glasses at a meeting table with a colleague" style="background:linear-gradient(135deg,#e9ecef,#8ea5bd 55%,#d5dbe2)"><div class="date">SEP<br>09<br>2017</div></div>
    <h3>Nemo enim ipsam voluptatem quia</h3>
    <p>Sed ut perspiciatis unde omnis iste natus error sit uptatem accusantium doloremque laudantium, totam rem aperiam, eaque ipsa quae ab illo inventore veritatis</p>
    <span class="btn-small">READ MORE</span>
  </article>
</section>

<footer class="section site-footer">
  <div class="col" style="left:97px;width:260px">
    <h5>SIGN UP FOR NEWSLETTER</h5>
    <p style="margin-top:14px">Excepteur sint occaecat cupidatat non proident, sunt in culpa qui officia deserunt</p>
    <div class="email-field">Enter email</div>
    <span class="btn-dark">SUBSCRIPTION</span>
  </div>
  <div class="col" style="left:421px;width:280px">
    <h5>CONTACT US</h5>
    <div class="addr" style="margin-top:18px"><svg width="12" height="16" viewBox="0 0 12 16"><path d="M6 0a6 6 0 016 6c0 4-6 10-6 10S0 10 0 6a6 6 0 016-6z" fill="#fff"/><circle cx="6" cy="6" r="2" fill="#2b4c9e"/></svg><span>Marcus Delbridge, 14 Harbour Row<br>Seaview Point, Queensland 4299</span></div>
    <div class="addr"><svg width="12" height="12" viewBox="0 0 24 24"><path d="M6.6 10.8a15 15 0 006.6 6.6l2.2-2.2a1 1 0 011-.25 11 11 0 003.6.6 1 1 0 011 1V20a1 1 0 01-1 1A17 17 0 013 4a1 1 0 011-1h3.5a1 1 0 011 1 11 11 0 00.6 3.6 1 1 0 01-.25 1z" fill="#fff"/></svg><span>Phone: 61 7 5550 2840<br>Fax: 61 7 5550 2841</span></div>
    <div class="addr"><svg width="13" height="10" viewBox="0 0 24 18"><rect x="0" y="0" width="24" height="18" fill="#fff"/><path d="M1 1l11 9 11-9" fill="none" stroke="#2b4c9e" stroke-width="2"/></svg><span>info@marcusdelbridge.com.au</span></div>
  </div>
  <div class="col" style="left:731px">
    <h5>QUICK LINKS</h5>
    <ul><li>Home</li><li>About Us</li><li>How It Works</li><li>Our Services</li><li>Blog</li><li>Contact</li></ul>
  </div>
  <div class="footer-name">Marcus Delbridge</div>
  <div class="socials"><i></i><i></i><i></i><i></i></div>
</footer>
<div class="copyright">©2016 - 2017 Marcus Delbridge, All Rights Reserved.</div>

</body>
</html>
```